Website redesign - vorelmik.com

We are looking to do a full redesign of vorelmik.com. Need a designer to come up overall layout and 3 specific pages and 3 different hero images.
Wireframes for the 3 pages are attached as well as site images. You don't have to follow the wireframes exactly, but instead the wireframe is there to show you the information that needs to be on each page. Feel free to rearrange as needed.
Our target market is self taught engineers. So definitely I want a more casual feel to it. I'm ok with fun bold colors as well. Really like websites that have the infinite scroll look/feel to them.
Looking to find a designer who will produce HTML and potentially even implement the HTML into our site checked in code.
HTML Code should be responsive/mobile first leveraging Bootstrap 4.
Attached files include:
0) Wireframe PDF
https://files.plomwerk.net/d/7Kx2pQmW9zLr4TbN8vYc3HsE5fJ/view?mode=share
1) Vorelmik Images zip 1
https://files.plomwerk.net/d/4Gt8nRvB2wQx6MkZ1pLd9YaC7hU/view?mode=share
2) Vorelmik Images zip 2
https://files.plomwerk.net/d/9Jw3sTcF5yNv1HqX8rKb2ZeM6dP/view?mode=share
Target Market(s)
I sell DIY Waterproof Electronics enclosures. Target audience is self taught DIY engineers
Coding
Coded - Design and coding required
Number of Pages Required
3 page
Colors
Designer to choose colors to be used in the design.
Look and feel

```html
<!DOCTYPE html>
<html lang="en">
<head>
<meta charset="utf-8">
<title>Vorelmik – Waterproof Project Boxes</title>
<link href="https://fonts.googleapis.com/css2?family=Lato:wght@400;700&family=Montserrat:wght@500;600&display=swap" rel="stylesheet">
<style>
:root{
  --brand:#2b2bc4;
  --brand-deep:#1c1cc8;
  --brand-soft:#3d3dcf;
  --accent:#e2b411;
  --ink:#1f1f4a;
  --body:#555566;
  --hero-bg:#dedff2;
  --quote-bg:#e2e2f7;
  --footer:#16164a;
  --card-line:#d6d6de;
}
*{box-sizing:border-box;margin:0;padding:0}
html,body{width:1200px;height:3883px;overflow:hidden;background:#fff;font-family:"Lato",sans-serif;color:var(--body)}
.page{position:relative;width:1200px;height:3883px}
.abs{position:absolute}
.btn{position:absolute;width:172px;height:46px;background:var(--accent);color:#fff;font-family:"Montserrat",sans-serif;font-weight:600;font-size:15px;display:flex;align-items:center;justify-content:center;letter-spacing:.2px}
.photo{position:absolute}

/* header */
.header{position:absolute;left:0;top:0;width:1200px;height:81px;background:#fff}
.logo{position:absolute;left:68px;top:14px;display:flex;align-items:center;gap:10px;font-family:"Lato",sans-serif;font-weight:700;font-size:38px;color:var(--brand)}
.logo-dot{width:12px;height:12px;border-radius:50%;background:var(--accent)}
.nav{position:absolute;top:32px;font-family:"Montserrat",sans-serif;font-size:15px;color:#222;font-weight:500}
.nav-active{position:absolute;left:333px;top:78px;width:104px;height:3px;background:#c6cc5a}
.sign-in{position:absolute;left:968px;top:0;width:116px;height:81px;background:var(--brand-deep);color:#fff;font-family:"Montserrat",sans-serif;font-weight:600;font-size:15px;display:flex;align-items:center;justify-content:center}
.sign-up{position:absolute;left:1084px;top:0;width:116px;height:81px;background:var(--accent);color:#fff;font-family:"Montserrat",sans-serif;font-weight:600;font-size:15px;display:flex;align-items:center;justify-content:center}

/* hero */
.hero{position:absolute;left:0;top:81px;width:1200px;height:558px;background:linear-gradient(90deg,#dcdcf3 0%,#e0e0ef 60%,#e6e6e8 100%)}
.hero-title{position:absolute;left:137px;top:145px;font-weight:700;font-size:36px;line-height:36px;color:var(--brand);width:420px}
.hero-sub{position:absolute;left:137px;top:264px;font-size:22px;color:var(--brand)}
.dots{position:absolute;left:560px;top:516px;display:flex;gap:9px}
.dots span{width:13px;height:13px;border-radius:50%;background:#9b9bab}
.dots span.ring{background:transparent;border:2px solid #9b9bab}

/* designer */
.accent-box{position:absolute;left:377px;top:898px;width:241px;height:157px;background:var(--brand-deep)}
.play{position:absolute;left:325px;top:842px;width:76px;height:76px;border-radius:50%;background:#fff;display:flex;align-items:center;justify-content:center}
.h2{position:absolute;font-weight:700;font-size:27px;line-height:37px;color:var(--ink)}
.para{position:absolute;font-size:15.5px;line-height:27px;color:var(--body)}

/* band */
.band{position:absolute;left:0;top:1126px;width:1200px;height:460px;background:linear-gradient(100deg,#4343cf 0%,#3434d2 50%,#1d1dca 100%)}
.band-title{position:absolute;left:137px;top:104px;width:330px;color:#fff;font-weight:700;font-size:28px;line-height:36px}

/* features */
.features{position:absolute;left:595px;top:1783px;list-style:none}
.features li{display:flex;align-items:center;gap:14px;height:36.5px;font-size:17px;color:#444}

/* testimonials */
.quotes{position:absolute;left:0;top:2097px;width:1200px;height:463px;background:var(--quote-bg)}
.quotes-title{position:absolute;left:0;top:56px;width:1200px;text-align:center;font-weight:700;font-size:28px;color:var(--ink)}
.quote-card{position:absolute;top:136px;width:418px;height:233px;background:#fff;box-shadow:0 4px 14px rgba(40,40,120,.08);padding:38px 48px 0 48px;font-size:17px;line-height:31px;color:#444}
.qmark{font-family:Georgia,serif;font-weight:700;font-size:40px;color:var(--brand);line-height:10px;vertical-align:-10px}
.author{margin-top:18px}
.arrow{position:absolute}

/* examples */
.ex-title{position:absolute;left:0;top:2612px;width:1200px;text-align:center;font-weight:700;font-size:31px;line-height:37px;color:var(--brand)}
.ex-card{position:absolute;width:275px;height:323px;border:2px solid var(--card-line);background:#fff;box-shadow:0 2px 6px rgba(0,0,0,.06)}
.ex-card .shot{position:absolute;left:40px;top:28px;width:191px;height:176px;border-radius:4px}
.ex-card .cap{position:absolute;left:0;bottom:18px;width:100%;text-align:center;font-weight:700;font-size:15px;line-height:21px;color:#333}

/* footer */
.footer{position:absolute;left:0;top:3805px;width:1200px;height:78px;background:var(--footer);color:#fff;font-size:16px}
.footer .copy{position:absolute;left:175px;top:29px}
.footer .follow{position:absolute;left:874px;top:29px;display:flex;align-items:center;gap:14px}
.social{font-size:14px;font-weight:700}
</style>
</head>
<body>
<div class="page">

  <header class="header">
    <div class="logo"><span class="logo-dot"></span>vorelmik</div>
    <span class="nav" style="left:333px">GET STARTED</span>
    <span class="nav" style="left:476px">DESIGNS</span>
    <span class="nav" style="left:583px">FAQS</span>
    <span class="nav" style="left:666px">VIDEOS</span>
    <span class="nav" style="left:764px">CONTACT US</span>
    <div class="nav-active"></div>
    <div class="sign-in">SIGN IN</div>
    <div class="sign-up">SIGN UP</div>
  </header>

  <section class="hero">
    <h1 class="hero-title">WATERPROOF PROJECT BOXES CUSTOMIZED TO YOUR EXACT NEEDS.</h1>
    <p class="hero-sub">(AT A FRACTION OF THE PRICE)</p>
    <div class="btn" style="left:137px;top:314px">GET STARTED</div>
    <div class="photo" role="img" aria-label="Stacked circuit boards mounted on black acrylic plates with standoffs" style="left:573px;top:100px;width:550px;height:309px;background:linear-gradient(160deg,#3c6b4a 0%,#2a2a2e 55%,#4a4a52 100%);border-radius:6px"></div>
    <div class="dots"><span class="ring"></span><span></span><span></span><span></span></div>
  </section>

  <section>
    <div class="accent-box"></div>
    <div class="photo" role="img" aria-label="Video still of wired electronics inside an open enclosure" style="left:133px;top:734px;width:459px;height:294px;background:linear-gradient(135deg,#d8d8d8 0%,#555 45%,#2d2d2d 70%,#b9b9b9 100%)"></div>
    <div class="play"><svg width="26" height="30" viewBox="0 0 26 30"><path d="M2 1 L25 15 L2 29 Z" fill="#111"/></svg></div>
    <h2 class="h2" style="left:671px;top:757px">Customize your Project<br>Box using our Designer</h2>
    <p class="para" style="left:672px;top:848px;width:420px">Etiam eleifend metus vitae adipiscing semper mauris ipsum iaculis elit congue gravida elit mi Agestas orci Curabitur pede Maecenas aliquet velit vel turpis Mauris neque metus malesuada nec ultricies</p>
    <div class="btn" style="left:672px;top:983px">GET STARTED</div>
  </section>

  <section class="band">
    <h2 class="band-title">Mounting Kits for all the popular water proof project boxes with many sizes to choose from</h2>
    <div class="btn" style="left:137px;top:279px">GET STARTED</div>
    <svg class="arrow" style="left:476px;top:180px" width="24" height="46" viewBox="0 0 24 46"><path d="M22 2 L3 23 L22 44" fill="none" stroke="#fff" stroke-width="2.5"/></svg>
    <svg class="arrow" style="left:1144px;top:180px" width="24" height="46" viewBox="0 0 24 46"><path d="M2 2 L21 23 L2 44" fill="none" stroke="#fff" stroke-width="2.5"/></svg>
    <div class="photo" role="img" aria-label="Three grey waterproof enclosures, two open showing mounted power supplies" style="left:513px;top:148px;width:617px;height:226px;background:linear-gradient(180deg,#d9d9de 0%,#c4c4ca 100%);border-radius:8px;opacity:.95"></div>
  </section>

  <section>
    <div class="photo" role="img" aria-label="Brown mounting plate with controller boards and a power supply attached" style="left:108px;top:1673px;width:435px;height:335px;background:linear-gradient(140deg,#8a7a66 0%,#6e604f 60%,#9a8c78 100%);border-radius:6px"></div>
    <h2 class="h2" style="left:595px;top:1688px">Vorelmik waterproof project boxes<br>were built by makers for makers</h2>
    <ul class="features">
      <li><svg width="18" height="18" viewBox="0 0 18 18"><circle cx="9" cy="9" r="7.8" fill="none" stroke="#333" stroke-width="1.4"/><path d="M5.2 9.3 L8 12 L13 6.3" fill="none" stroke="#333" stroke-width="1.6"/></svg>Design to your specifications</li>
      <li><svg width="18" height="18" viewBox="0 0 18 18"><circle cx="9" cy="9" r="7.8" fill="none" stroke="#333" stroke-width="1.4"/><path d="M5.2 9.3 L8 12 L13 6.3" fill="none" stroke="#333" stroke-width="1.6"/></svg>Maker components: Ardel, Quincefruit Board, Steadyvolt Power</li>
      <li><svg width="18" height="18" viewBox="0 0 18 18"><circle cx="9" cy="9" r="7.8" fill="none" stroke="#333" stroke-width="1.4"/><path d="M5.2 9.3 L8 12 L13 6.3" fill="none" stroke="#333" stroke-width="1.6"/></svg>Detailed build instructions, videos, walkthroughs</li>
      <li><svg width="18" height="18" viewBox="0 0 18 18"><circle cx="9" cy="9" r="7.8" fill="none" stroke="#333" stroke-width="1.4"/><path d="M5.2 9.3 L8 12 L13 6.3" fill="none" stroke="#333" stroke-width="1.6"/></svg>DIY made to look professional</li>
    </ul>
    <div class="btn" style="left:595px;top:1946px">GET STARTED</div>
  </section>

  <section class="quotes">
    <h2 class="quotes-title">What our Customers Have to Say</h2>
    <svg class="arrow" style="left:98px;top:218px" width="28" height="52" viewBox="0 0 28 52"><path d="M25 2 L4 26 L25 50" fill="none" stroke="var(--brand)" stroke-width="2.5"/><path d="M25 10 L10 26 L25 42" fill="none" stroke="var(--brand)" stroke-width="1.5"/></svg>
    <svg class="arrow" style="left:1062px;top:218px" width="28" height="52" viewBox="0 0 28 52"><path d="M3 2 L24 26 L3 50" fill="none" stroke="var(--brand)" stroke-width="2.5"/><path d="M3 10 L18 26 L3 42" fill="none" stroke="var(--brand)" stroke-width="1.5"/></svg>
    <div class="quote-card" style="left:167px">
      <p><span class="qmark">&ldquo;</span> Great work at a reasonable cost. I can't recommend them enough. If you're doing custom boxes for light shows, this is where you go. <span class="qmark">&rdquo;</span></p>
      <p class="author">-Aren T</p>
    </div>
    <div class="quote-card" style="left:615px">
      <p><span class="qmark">&ldquo;</span> Fantastic service/product.. whether you simply generate the design and do all of the fabrication yourself or simply order the kits. <span class="qmark">&rdquo;</span></p>
      <p class="author">-Milo K.</p>
    </div>
  </section>

  <section>
    <h2 class="ex-title">See Real Examples from<br>our Customers</h2>

    <div class="ex-card" style="left:157px;top:2712px"><div class="shot" role="img" aria-label="Two-tier controller board kit on black plates" style="background:linear-gradient(160deg,#4d7a52,#222 70%)"></div><p class="cap">KTR BX8-72 w/ P16v3 +<br>Expansion board</p></div>
    <div class="ex-card" style="left:466px;top:2712px"><div class="shot" role="img" aria-label="Controller board with terminal blocks on black mounting plate" style="background:linear-gradient(160deg,#5c8a4a,#2a2a2a 70%)"></div><p class="cap">KTR BX8-72 w/ P16v3 +<br>Expansion board</p></div>
    <div class="ex-card" style="left:776px;top:2712px"><div class="shot" role="img" aria-label="Relay board on black acrylic plate with standoffs" style="background:linear-gradient(160deg,#555,#1e1e1e 70%)"></div><p class="cap">KTR BX8-72 w/ P16v3 +<br>Expansion board</p></div>

    <div class="ex-card" style="left:157px;top:3059px"><div class="shot" role="img" aria-label="Power supply stacked above controller board" style="background:linear-gradient(160deg,#bdbdbd,#2a2a2a 70%)"></div><p class="cap">KTR BX8-72 w/ P16v3 +<br>Expansion board</p></div>
    <div class="ex-card" style="left:466px;top:3059px"><div class="shot" role="img" aria-label="Power supply mounted over a small board on black plate" style="background:linear-gradient(160deg,#c4c4c4,#242424 70%)"></div><p class="cap">KTR BX8-72 w/ P16v3 +<br>Expansion board</p></div>
    <div class="ex-card" style="left:776px;top:3059px"><div class="shot" role="img" aria-label="Two power supplies on a black base plate" style="background:linear-gradient(180deg,#fff 10%,#bcbcbc 35%,#2a2a2a 70%,#fff 90%)"></div><p class="cap">KTR BX8-72 w/ P16v3 +<br>Expansion board</p></div>

    <div class="ex-card" style="left:155px;top:3408px"><div class="shot" role="img" aria-label="Translucent pink waterproof enclosure" style="background:linear-gradient(160deg,#f6eaf2,#e4d4e2)"></div><p class="cap">KTR BX8-72 w/ P16v3 +<br>Expansion board</p></div>
    <div class="ex-card" style="left:464px;top:3408px"><div class="shot" role="img" aria-label="Board and fan mounted on black plate" style="background:linear-gradient(160deg,#3a3a3a,#1c1c1c 70%)"></div><p class="cap">KTR BX8-72 w/ P16v3 +<br>Expansion board</p></div>
    <div class="ex-card" style="left:774px;top:3408px"><div class="shot" role="img" aria-label="Power supply beside green controller board" style="background:linear-gradient(160deg,#b8b8b8,#3d6a47 55%,#222)"></div><p class="cap">KTR BX8-72 w/ P16v3 +<br>Expansion board</p></div>
  </section>

  <footer class="footer">
    <p class="copy">Copyright 2020 @ vorelmik designer.</p>
    <div class="follow">Follow Us: <span class="social">Pagebook</span><span class="social">Clipstream</span></div>
  </footer>

</div>
</body>
</html>
```